U.S. Popcorn company needs business cards

We are a popcorn company that manufactures popcorn and sells it to grocery stores worldwide. Our theme is "Americana" and our logo is U.S. route 66 which is the most famous highway in the U.S.

We would like the design to be simple and to use both sides. On the back side we would like to see just the logo and website. The front would be normal details

Target Market(s)

Wholesalers, grocers and distributors

Industry/Entity Type

Manufacture

Contact Information for Business Card

Business name: Prairie Lantern Popcorn
Phone: +1 555 308 4726
Email: Dale@prairielanternpopcorn.com
website: www.prairielanternpopcorn.com
Tag Line: "FRESH FROM THE KETTLE"
Name: Dale Whitcombe
Title: Founder/President

Requirements
Must have
• Either this design should be fun or clean and simple. I will let you show me your thougths.
Nice to have
• Anything that ties in the real Hwy Route 66.
• Colors might need to be red, white and blue incorporated.
Should not have
• Not be too busy.

```html
<!DOCTYPE html>
<html lang="en">
<head>
<meta charset="utf-8">
<title>Prairie Lantern Popcorn – Business Card</title>
<link href="https://fonts.googleapis.com/css2?family=Open+Sans:wght@400;600;700&display=swap" rel="stylesheet">
<style>
  :root {
    --backdrop: #3b3532;
    --card: #0d0d0d;
    --card-edge: #1c1c1c;
    --accent-red: #e0202a;
    --text-white: #f2f2f2;
    --text-silver: #cfcfcf;
  }
  * { margin: 0; padding: 0; box-sizing: border-box; }
  html, body {
    width: 1200px; height: 900px; overflow: hidden;
    background: var(--backdrop);
    font-family: "Open Sans", Arial, sans-serif;
  }
  .canvas {
    position: relative; width: 1200px; height: 900px;
    display: flex; align-items: center; justify-content: center; gap: 40px;
  }
  .card {
    position: relative; width: 540px; height: 310px;
    background: var(--card);
    border: 1px solid var(--card-edge);
    box-shadow: 0 10px 30px rgba(0,0,0,.45);
  }
  /* Front */
  .brand-mark {
    position: absolute; left: 40px; top: 95px; width: 190px;
    display: flex; align-items: center; gap: 12px;
  }
  .brand-mark .dot {
    flex: none; width: 16px; height: 16px; border-radius: 50%;
    background: var(--text-white);
  }
  .brand-mark .brand-name {
    color: var(--text-white); font-weight: 700; font-size: 24px;
    line-height: 1.15; text-transform: uppercase;
  }
  .divider {
    position: absolute; left: 250px; top: 70px; width: 1px; height: 130px;
    background: linear-gradient(var(--accent-red), rgba(224,32,42,0));
  }
  .contact-block { position: absolute; left: 272px; top: 64px; }
  .person-name {
    color: var(--accent-red); font-weight: 700; font-size: 17px; line-height: 1.2;
  }
  .person-title { color: var(--text-white); font-size: 13px; margin-bottom: 22px; }
  .contact-list { list-style: none; }
  .contact-list li {
    display: flex; align-items: center; gap: 9px;
    color: var(--text-white); font-size: 13px; line-height: 20px;
    white-space: nowrap;
  }
  .contact-list svg { width: 11px; height: 11px; flex: none; fill: var(--accent-red); }
  .tagline {
    position: absolute; left: 40px; bottom: 34px;
    color: var(--accent-red); font-size: 16px; letter-spacing: .3px;
  }
  /* Back */
  .card-back { display: flex; align-items: center; justify-content: center; }
  .card-back .brand-mark { position: static; width: 230px; }
  .card-back .dot { background: var(--text-silver); }
  .card-back .brand-name { color: var(--text-silver); font-size: 28px; }
</style>
</head>
<body>
<main class="canvas">
  <section class="card card-front" aria-label="Business card front">
    <div class="brand-mark">
      <span class="dot"></span>
      <span class="brand-name">Prairie Lantern Popcorn</span>
    </div>
    <div class="divider"></div>
    <div class="contact-block">
      <p class="person-name">Dale Whitcombe</p>
      <p class="person-title">Founder/President</p>
      <ul class="contact-list">
        <li>
          <svg viewBox="0 0 24 24" aria-hidden="true"><path d="M6.6 10.8a15.1 15.1 0 0 0 6.6 6.6l2.2-2.2a1 1 0 0 1 1-.25 11.4 11.4 0 0 0 3.6.57 1 1 0 0 1 1 1V20a1 1 0 0 1-1 1A17 17 0 0 1 3 4a1 1 0 0 1 1-1h3.5a1 1 0 0 1 1 1c0 1.25.2 2.46.57 3.6a1 1 0 0 1-.25 1z"/></svg>
          +1 555 308 4726
        </li>
        <li>
          <svg viewBox="0 0 24 24" aria-hidden="true"><path d="M2 5h20v14H2z"/><path d="M3 6l9 7 9-7" stroke="#0d0d0d" stroke-width="2" fill="none"/></svg>
          Dale@prairielanternpopcorn.com
        </li>
        <li>
          <svg viewBox="0 0 24 24" aria-hidden="true"><circle cx="12" cy="12" r="10"/><path d="M2 12h20M12 2c3 3 3 17 0 20M12 2c-3 3-3 17 0 20" stroke="#0d0d0d" stroke-width="1.6" fill="none"/></svg>
          www.prairielanternpopcorn.com
        </li>
      </ul>
    </div>
    <p class="tagline">FRESH FROM THE KETTLE</p>
  </section>

  <section class="card card-back" aria-label="Business card back">
    <div class="brand-mark">
      <span class="dot"></span>
      <span class="brand-name">Prairie Lantern Popcorn</span>
    </div>
  </section>
</main>
</body>
</html>
```